Business Card Design for Property Development Company Director

I am looking for a professional and unforgettable business card design for our Director of our Property Development Company.
Please see attached .pptx file to find out what information to include. You don't have to follow the exact format shown in the file - I am interested to see your creative flair using the information provided.

```html
<!DOCTYPE html>
<html lang="en">
<head>
<meta charset="utf-8">
<title>Calworth Property Group – Business Card</title>
<link href="https://fonts.googleapis.com/css2?family=Lato:wght@400;700&display=swap" rel="stylesheet">
<style>
  :root {
    --brand-blue: #0d55a6;
    --ink-grey: #5a5a5a;
    --text-dark: #3a3a3a;
    --rule-grey: #b9b9b9;
    --paper: #ffffff;
    --backdrop: #d4d4d4;
  }
  * { margin: 0; padding: 0; box-sizing: border-box; }
  html, body { width: 1200px; height: 802px; overflow: hidden; }
  body {
    background: var(--backdrop);
    font-family: "Lato", sans-serif;
    position: relative;
  }
  .card {
    position: absolute;
    top: 274px;
    width: 443px;
    height: 264px;
    overflow: hidden;
    box-shadow: 0 3px 8px rgba(0,0,0,0.25);
  }
  .card--front { left: 136px; background: var(--paper); }
  .card--back { left: 624px; background: var(--brand-blue); color: #fff; }

  .wordmark {
    position: absolute;
    display: flex;
    align-items: center;
    gap: 10px;
    font-weight: 700;
  }
  .wordmark__square { width: 40px; height: 40px; flex: none; }
  .wordmark__name { font-size: 30px; line-height: 1; letter-spacing: 0.5px; }
  .wordmark__sub { font-size: 11.5px; letter-spacing: 3.4px; margin-top: 4px; }

  .card--front .wordmark { right: 29px; top: 50px; color: var(--brand-blue); }
  .card--front .wordmark__square { background: var(--brand-blue); }

  .holder { position: absolute; left: 29px; top: 144px; }
  .holder__name { font-size: 17.5px; font-weight: 700; color: var(--ink-grey); letter-spacing: -0.2px; line-height: 20px; }
  .holder__name span { color: var(--brand-blue); }
  .holder__role { font-size: 13px; color: var(--ink-grey); line-height: 14px; }
  .holder__rule {
    position: absolute; left: 79px; top: 172px; width: 337px; height: 1px;
    background: var(--rule-grey);
  }

  .contacts { position: absolute; left: 28px; top: 192px; list-style: none; font-size: 12.5px; color: var(--text-dark); }
  .contacts li { display: flex; align-items: center; gap: 5px; height: 16px; }
  .contacts svg { width: 11px; height: 11px; fill: var(--brand-blue); }

  .licence { position: absolute; right: 23px; top: 225px; font-size: 11.5px; color: var(--text-dark); }
  .licence span { color: var(--brand-blue); }

  .tagline { position: absolute; top: 41px; width: 100%; text-align: center; font-size: 13px; line-height: 16px; }
  .card--back .wordmark { left: 50%; top: 118px; transform: translateX(-50%); color: #fff; }
  .card--back .wordmark__square { background: #fff; width: 46px; height: 46px; }
  .card--back .wordmark__name { font-size: 35px; }
  .card--back .wordmark__sub { font-size: 13px; letter-spacing: 4px; }
  .back__rule { position: absolute; left: 61px; top: 217px; width: 321px; height: 1px; background: rgba(255,255,255,0.35); }
  .offer { position: absolute; top: 226px; width: 100%; text-align: center; font-size: 12px; }
</style>
</head>
<body>
  <section class="card card--front" aria-label="Business card front">
    <div class="wordmark">
      <div class="wordmark__square"></div>
      <div>
        <div class="wordmark__name">CALWORTH</div>
        <div class="wordmark__sub">PROPERTY GROUP</div>
      </div>
    </div>

    <div class="holder">
      <div class="holder__name">DANIEL <span>MARSH</span></div>
      <div class="holder__role">Director</div>
    </div>
    <div class="holder__rule"></div>

    <ul class="contacts">
      <li><svg viewBox="0 0 24 24"><path d="M6.6 10.8c1.4 2.8 3.8 5.1 6.6 6.6l2.2-2.2c.3-.3.7-.4 1-.2 1.1.4 2.3.6 3.6.6.6 0 1 .4 1 1V20c0 .6-.4 1-1 1C10.6 21 3 13.4 3 4c0-.6.4-1 1-1h3.5c.6 0 1 .4 1 1 0 1.3.2 2.5.6 3.6.1.3 0 .7-.2 1z"/></svg>0400 218 365</li>
      <li><svg viewBox="0 0 24 24"><path d="M2 5h20v14H2z M2 5l10 8 10-8" fill="none" stroke="#0d55a6" stroke-width="2.5"/></svg>daniel@calworth.com.au</li>
      <li><svg viewBox="0 0 24 24"><circle cx="12" cy="12" r="10"/></svg>www.calworth.com.au</li>
    </ul>

    <div class="licence"><span>Real Estate Lic:</span>&nbsp; 5102936 &amp; 5102937</div>
  </section>

  <section class="card card--back" aria-label="Business card back">
    <p class="tagline">PROPERTY DEVELOPMENT<br>&amp; SITE ACQUISITION SPECIALISTS</p>
    <div class="wordmark">
      <div class="wordmark__square"></div>
      <div>
        <div class="wordmark__name">CALWORTH</div>
        <div class="wordmark__sub">PROPERTY GROUP</div>
      </div>
    </div>
    <div class="back__rule"></div>
    <p class="offer">Ask me about our INVESTMENT &amp; PARTNERSHIP opportunities</p>
  </section>
</body>
</html>
```